Design NEW business card

We would like a business card using the colour deep red wine or dark navy blue textured background (patterned or not, open to suggestions) with a high gloss debossed rose gold/copper RM Roland Mercer Jewellery business name (Provided). I have included images for your review we would like to keep our currently logo and business name on the front but you can change the layout and positioning. For the back of the card we are open to all suggestions/variations.
Business
Use our current RM Roland Mercer Jewellery logo (Provided image)

```html
<!DOCTYPE html>
<html lang="en">
<head>
<meta charset="utf-8">
<title>Roland Mercer Jewellery – Business Card</title>
<link href="https://fonts.googleapis.com/css2?family=Montserrat:wght@300;400;600&display=swap" rel="stylesheet">
<style>
  :root{
    --backdrop:#c8c8c8;
    --wine:#55202a;
    --paper:#f4f4f3;
    --rose-gold:#c8916c;
    --rose-gold-deep:#a77557;
    --rose-gold-light:#ddb08e;
    --grey-text:#a9a9a9;
    --white:#ffffff;
  }
  *{margin:0;padding:0;box-sizing:border-box;}
  html,body{width:1200px;height:960px;overflow:hidden;}
  body{
    background:var(--backdrop);
    font-family:"Montserrat",sans-serif;
    position:relative;
  }
  .card{
    position:absolute;
    box-shadow:0 3px 8px rgba(0,0,0,.25);
    overflow:hidden;
  }
  .brand-mark{
    position:absolute;
    border:2px solid var(--rose-gold);
    border-radius:50%;
  }
  /* Front */
  .card--front{
    left:320px;top:105px;width:610px;height:355px;
    background:var(--wine);
  }
  .card--front .brand-mark{
    left:128px;top:78px;width:120px;height:120px;
  }
  .front-brand{
    position:absolute;left:196px;top:224px;
    color:var(--rose-gold);
    font-weight:300;
    white-space:nowrap;
  }
  .front-brand__name{
    display:block;
    font-size:27px;letter-spacing:.16em;line-height:32px;
  }
  .front-brand__trade{
    display:block;margin-top:5px;
    font-size:11px;letter-spacing:2.45em;line-height:14px;
  }
  /* Back */
  .card--back{
    left:321px;top:493px;width:600px;height:342px;
    background:var(--paper);
  }
  .card--back .brand-mark{
    left:34px;top:34px;width:80px;height:80px;
  }
  .back-brand{
    position:absolute;left:76px;top:124px;
    color:var(--rose-gold);
    font-weight:300;
    white-space:nowrap;
  }
  .back-brand__name{
    display:block;font-size:17px;letter-spacing:.12em;line-height:21px;
  }
  .back-brand__trade{
    display:block;margin-top:3px;
    font-size:8px;letter-spacing:1.95em;line-height:10px;
  }
  .person{
    position:absolute;right:41px;top:46px;text-align:right;
  }
  .person__name{
    display:block;font-size:17px;font-weight:400;
    color:var(--rose-gold-deep);letter-spacing:.01em;
  }
  .person__role{
    display:block;margin-top:3px;font-size:12px;font-weight:400;
    color:var(--grey-text);letter-spacing:.04em;
  }
  .wave{
    position:absolute;left:0;top:0;width:600px;height:342px;
  }
  .contact{
    position:absolute;left:40px;right:0;top:263px;
    text-align:center;color:var(--white);
    font-size:13px;font-weight:400;line-height:19px;
    font-style:normal;
  }
  .contact b{font-weight:600;}
</style>
</head>
<body>

<section class="card card--front" aria-label="Card front">
  <span class="brand-mark" aria-hidden="true"></span>
  <div class="front-brand">
    <span class="front-brand__name">ROLAND MERCER</span>
    <span class="front-brand__trade">JEWELLERY</span>
  </div>
</section>

<section class="card card--back" aria-label="Card back">
  <svg class="wave" viewBox="0 0 600 342" aria-hidden="true">
    <defs>
      <radialGradient id="roseGoldSheen" cx="0.58" cy="0.45" r="0.6">
        <stop offset="0" stop-color="#ddb08e"/>
        <stop offset="0.6" stop-color="#c8956f"/>
        <stop offset="1" stop-color="#a77557"/>
      </radialGradient>
    </defs>
    <path d="M0 342 L0 338 C120 290 210 165 345 162 C440 160 520 215 600 258 L600 342 Z" fill="url(#roseGoldSheen)"/>
  </svg>

  <span class="brand-mark" aria-hidden="true"></span>
  <div class="back-brand">
    <span class="back-brand__name">ROLAND MERCER</span>
    <span class="back-brand__trade">JEWELLERY</span>
  </div>

  <div class="person">
    <span class="person__name">DANIEL HART</span>
    <span class="person__role">CEO/FOUNDER</span>
  </div>

  <address class="contact">
    2140 Willow Crest Road, Juneau, Alaska 34512<br>
    <b>P:</b> 907 214 3381 <b>M:</b> 907 552 7460 <b>F:</b> 907 318 6025<br>
    <b>E:</b> hello@rmjewellery.com <b>W:</b> rmjewellery.com
  </address>
</section>

</body>
</html>
```